Unique Business Card Design

Unique Business Card design for our orthotic and prosthetic company. Our logo is on our website, color is light blue. Unique shape (artificial leg shaped, vertical, etc..) preferred. Logo, business name, individual name and basic demographics needed.

Industry/Entity Type

Business

Contact Information for Business Card

Logo, Industry, Phone # Logo, "Prosthetic & Orthotic Services" Place to add individual name and contact info

Colors
cee9f5

Requirements
Must have
• The icon must be there, placement of "Prosthetic & Orthotic Services" can be moved
Nice to have
• Like the mix of light blue, and a little darker blue. One design included the icons from my website which was a nice touch

```html
<!DOCTYPE html>
<html lang="en">
<head>
<meta charset="utf-8">
<title>Stridewell Inc. — Business Card</title>
<link rel="stylesheet" href="https://fonts.googleapis.com/css2?family=Open+Sans:wght@400;600;700&display=swap">
<style>
  :root {
    --brand-blue: #165fad;
    --ink: #3f4448;
    --paper: #ffffff;
    --backdrop: #e8ebea;
    --edge: #cfd3d3;
  }
  * { box-sizing: border-box; margin: 0; padding: 0; }
  html, body { width: 1200px; height: 812px; overflow: hidden; }
  body {
    background: var(--backdrop);
    font-family: "Open Sans", sans-serif;
    color: var(--ink);
    position: relative;
  }
  .card {
    position: absolute;
    top: 246px;
    width: 540px;
    height: 310px;
    background: var(--paper);
    box-shadow: 0 3px 0 var(--edge), 0 10px 24px rgba(0,0,0,0.12);
    overflow: hidden;
  }
  .card--front { left: 30px; }
  .card--back { left: 630px; }

  /* Front */
  .front-lockup {
    position: absolute;
    left: 110px; top: 108px;
    display: flex; align-items: center; gap: 22px;
  }
  .mark-circle {
    width: 86px; height: 86px; border-radius: 50%;
    background: var(--brand-blue); flex: none;
  }
  .wordmark {
    font-weight: 700;
    color: var(--brand-blue);
    font-size: 27px;
    letter-spacing: 0.5px;
    line-height: 1;
    padding-bottom: 6px;
    border-bottom: 2px solid var(--brand-blue);
  }
  .tagline {
    margin-top: 5px;
    font-size: 13px;
    color: var(--brand-blue);
    letter-spacing: 0.2px;
  }

  /* Back */
  .side-panel {
    position: absolute; left: 0; top: 0; bottom: 0;
    width: 200px;
    background: var(--brand-blue);
    display: flex; align-items: center; justify-content: center;
  }
  .side-panel .panel-circle {
    width: 146px; height: 146px; border-radius: 50%;
    background: var(--paper);
  }
  .details {
    position: absolute; left: 228px; top: 26px; right: 20px;
  }
  .person-name {
    font-size: 19px; color: var(--brand-blue); font-weight: 400;
  }
  .person-name strong { font-weight: 700; }
  .person-name .credentials { font-size: 12px; }
  .contact-lines {
    margin-top: 3px;
    font-size: 12.5px; line-height: 1.45;
  }
  .back-lockup { margin-top: 18px; }
  .back-lockup .wordmark { font-size: 25px; }
  .phone-list {
    list-style: none;
    margin-top: 16px;
    font-size: 12.5px; line-height: 1.6;
  }
  .phone-list li { display: flex; align-items: center; gap: 8px; }
  .phone-list svg { width: 13px; height: 13px; fill: var(--brand-blue); flex: none; }
</style>
</head>
<body>

<section class="card card--front" aria-label="Card front">
  <div class="front-lockup">
    <div class="mark-circle"></div>
    <div>
      <div class="wordmark">STRIDEWELL INC.</div>
      <div class="tagline">Prosthetic &amp; Orthotic Services</div>
    </div>
  </div>
</section>

<section class="card card--back" aria-label="Card back">
  <div class="side-panel"><div class="panel-circle"></div></div>
  <div class="details">
    <div class="person-name"><strong>Mirela</strong> Castov, <span class="credentials">CO LPO</span></div>
    <div class="contact-lines">
      Mcastov@stridewellinc.com<br>
      2280 W. 14th St.<br>
      Harbor City, NY 10230
    </div>
    <div class="back-lockup">
      <div class="wordmark">STRIDEWELL INC.</div>
      <div class="tagline">Prosthetic &amp; Orthotic Services</div>
    </div>
    <ul class="phone-list">
      <li><svg viewBox="0 0 16 16" aria-hidden="true"><path d="M3 1l3 3-1.5 2a9 9 0 0 0 5.5 5.5L12 10l3 3-2 2C7 15 1 9 1 3z"/></svg>555.014.2200</li>
      <li><svg viewBox="0 0 16 16" aria-hidden="true"><rect x="4" y="1" width="8" height="5"/><rect x="1" y="6" width="14" height="7" rx="1"/><rect x="4" y="11" width="8" height="4" fill="#fff"/></svg>555.014.2290</li>
      <li><svg viewBox="0 0 16 16" aria-hidden="true"><path d="M4 0h8a1 1 0 0 1 1 1v14a1 1 0 0 1-1 1H4a1 1 0 0 1-1-1V1a1 1 0 0 1 1-1zm1 2v10h6V2z"/></svg>555-017-3381</li>
      <li><svg viewBox="0 0 16 16" aria-hidden="true"><circle cx="8" cy="8" r="7"/><path d="M1 8h14M8 1c3 3 3 11 0 14M8 1c-3 3-3 11 0 14" stroke="#fff" stroke-width="1" fill="none"/></svg>www.stridewellinc.com</li>
    </ul>
  </div>
</section>

</body>
</html>
```